Rultan Staffing Full Length Retractable Office Banner

I need a design for a full-length retractable banner and A-Frame Sign for each of my offices. I have included designs that have been incorporated into a poster and tri-fold as a sample. I would like to see a colorful eyecatching banner that focuses on people. Would like to see some diversity with men and woman and different races.
Rultan Staffing is a light industrial staffing firm. www.RultanStaffing.example

Target Market(s)

Job seekers looking for employment

Industry/Entity Type

Staffing / Recruiting

Font styles to use
Other font styles liked:
• Professional yet fun

Requirements
Must have
• Eye catching design with young hip vibe.
Nice to have
• primary colors with light industrial type jobs

```html
<!DOCTYPE html>
<html lang="en">
<head>
<meta charset="utf-8">
<title>Rultan Staffing – Retractable Banner</title>
<link rel="stylesheet" href="https://fonts.googleapis.com/css2?family=Oswald:wght@700&family=Montserrat:wght@400&display=swap">
<style>
  :root {
    --red: #e53127;
    --green: #0e7a3c;
    --yellow: #e8c31a;
    --navy: #272762;
    --white: #ffffff;
    --sign: #ece7e1;
    --ink: #262626;
    --photo-a: #f3efe9;
    --photo-b: #d9c2a8;
    --photo-c: #b9dcd6;
  }
  html, body {
    margin: 0;
    padding: 0;
    width: 1200px;
    height: 2461px;
    overflow: hidden;
    background: var(--white);
  }
  .banner {
    display: block;
    width: 1200px;
    height: 2461px;
  }
  .brand-name { font-family: "Oswald", sans-serif; font-weight: 700; fill: var(--navy); }
  .headline { font-family: "Oswald", sans-serif; font-weight: 700; }
  .headline--red { fill: var(--red); }
  .headline--green { fill: var(--green); }
  .headline--yellow { fill: var(--yellow); }
  .headline--navy { fill: var(--navy); }
  .sign-board { fill: var(--sign); }
  .sign-text { font-family: "Oswald", sans-serif; font-weight: 700; fill: var(--ink); }
  .footer-band { fill: var(--navy); }
  .footer-strip { fill: var(--red); }
  .footer-url { font-family: "Montserrat", sans-serif; font-weight: 400; fill: var(--white); }
</style>
</head>
<body>
<svg class="banner" viewBox="0 0 1200 2461" xmlns="http://www.w3.org/2000/svg">
  <defs>
    <linearGradient id="team-photo-tone" x1="0" y1="0" x2="1" y2="1">
      <stop offset="0" stop-color="var(--photo-a)"/>
      <stop offset="0.5" stop-color="var(--photo-b)"/>
      <stop offset="1" stop-color="var(--photo-c)"/>
    </linearGradient>
    <radialGradient id="sign-photo-tone" cx="0.5" cy="0.5" r="0.6">
      <stop offset="0" stop-color="#f2f2f2"/>
      <stop offset="1" stop-color="#ffffff"/>
    </radialGradient>
  </defs>

  <!-- Brand -->
  <g class="brand">
    <text class="brand-name" x="600" y="300" text-anchor="middle" font-size="170" textLength="680" lengthAdjust="spacingAndGlyphs">Rultan Staffing</text>
  </g>

  <!-- Team photo area -->
  <rect x="0" y="430" width="1200" height="760" fill="url(#team-photo-tone)" role="img" aria-label="Photo of a diverse group of smiling young men and women giving thumbs up"/>

  <!-- Wave divider -->
  <g class="wave">
    <path d="M0,1125 C250,1010 550,1050 750,1090 C950,1120 1100,1060 1200,1010 L1200,1300 L0,1300 Z" fill="var(--navy)"/>
    <path d="M0,1152 C250,1062 550,1082 750,1112 C950,1142 1100,1118 1200,1098 L1200,1300 L0,1300 Z" fill="var(--red)"/>
    <path d="M0,1180 C250,1092 550,1112 750,1142 C950,1168 1100,1150 1200,1138 L1200,1300 L0,1300 Z" fill="var(--white)"/>
  </g>

  <!-- Headline -->
  <g class="headline">
    <text class="headline headline--red" x="88" y="1372" font-size="230" textLength="1027" lengthAdjust="spacingAndGlyphs">CONNECTING</text>
    <text class="headline headline--green" x="88" y="1570" font-size="230" textLength="1024" lengthAdjust="spacingAndGlyphs">GREAT PEOPLE</text>
    <text class="headline headline--yellow" x="495" y="1640" font-size="82" textLength="200" lengthAdjust="spacingAndGlyphs">WITH</text>
    <text class="headline headline--navy" x="90" y="1770" font-size="135" textLength="1020" lengthAdjust="spacingAndGlyphs">GREAT ORGANIZATIONS!</text>
  </g>

  <!-- Hiring sign -->
  <rect x="180" y="1790" width="840" height="540" fill="url(#sign-photo-tone)" role="img" aria-label="Photo of hands holding up a cardboard sign"/>
  <g class="hiring-sign">
    <rect class="sign-board" x="278" y="1840" width="647" height="428"/>
    <text class="sign-text" x="375" y="2055" font-size="190" textLength="455" lengthAdjust="spacingAndGlyphs">ALWAYS</text>
    <text class="sign-text" x="400" y="2210" font-size="190" textLength="410" lengthAdjust="spacingAndGlyphs">HIRING</text>
    <rect x="383" y="2228" width="108" height="16" fill="var(--red)"/>
    <rect x="491" y="2228" width="108" height="16" fill="var(--green)"/>
    <rect x="599" y="2228" width="112" height="16" fill="var(--yellow)"/>
    <rect x="711" y="2228" width="117" height="16" fill="var(--navy)"/>
  </g>

  <!-- Footer -->
  <g class="footer">
    <rect class="footer-strip" x="0" y="2318" width="1200" height="16"/>
    <rect class="footer-band" x="0" y="2334" width="1200" height="127"/>
    <text class="footer-url" x="600" y="2432" text-anchor="middle" font-size="66" textLength="980" lengthAdjust="spacing">www.RultanStaffing.example</text>
  </g>
</svg>
</body>
</html>
```